Business card design needed to incorporate existing logo

We need a business card for a new modern Accounting & Business Solutions company call TelmaNord Partners.com.au servicing all of Australia.
My tagline is Steady Ledger Answers... that deliver.

We specialise in Cloud Accounting and this is our primary focus. We also provide tax representation, debt recovery, computer, tablet and smart phone sales.

I would like a design that uses my corporate, trustworthy colours of blue/white, black/grey however am open to suggestion. I have attached my logo to go on the card somewhere,of which you will see the colour scheme.

I am after a card that STANDS OUT, somewhere between it not being too busy and not being a baron waste of space.

A 'cloud' incorporated in the design may work well, up to your artistic judgement. I know what I like when I see it; it is harder to put into words!

Excited to see your ideas!
I have added my logo predominately (blue/white) and for additional opportunity have added my reverse logo (darker one). I have used the blue/white on my website and letterhead. I will be using both on my vehicle signage.

Target Market(s)

Tradesmen and small-medium businesses of all descriptions Australia-wide

Industry/Entity Type

Debt

Contact Information for Business Card

Doug Hallett
Principal (optional)
TelmaNord Partners.com.au
Steady Ledger Answers... that deliver

P: 1800 493 518
M: 0412 658 071 (optional)
W: www.telmanordpartners.com.au
E: admin@telmanordpartners.com.au

Logo Text

Steady Ledger Answers... that deliver!

Logo styles of interest
Wordmark Logo
Requirements
Must have
• Must look professional and of high quality not cheap.

My logo and my tagline 'Steady Ledger Answers... that deliver'.

I have my colourscheme in mind as per my attached logo, however am open to suggestion. I want to see what you can create that I would not have thought of.

Modern, innovative.
Something I won't look at and think, 'I could have done that myself'.

Must be able to be printed on Prinvo 300gm premium cards and the artwork provided to me.
Nice to have
• Title of Principal is optional depending on space and judement call of look/fee.
M: (mobile) number is also optional as above.

Somthing cloud related given the Cloud Accounting aspect may be relevant. I leave it to your artistic design and judgement.
Should not have
• Must not look cheap.

```html
<!DOCTYPE html>
<html lang="en">
<head>
<meta charset="utf-8">
<title>TelmaNord Partners – Business Card</title>
<link rel="stylesheet" href="https://fonts.googleapis.com/css2?family=Montserrat:wght@400;500;700&display=swap">
<style>
  :root {
    --backdrop: #17181d;
    --navy: #13215e;
    --navy-deep: #0d1848;
    --brand-blue: #1577c0;
    --sky: #3b8fd6;
    --ink: #232838;
    --grey: #5a5f6e;
    --white: #ffffff;
  }
  * { box-sizing: border-box; margin: 0; padding: 0; }
  html, body {
    width: 1200px; height: 675px; overflow: hidden;
    background: var(--backdrop);
    font-family: "Montserrat", sans-serif;
  }
  .canvas {
    width: 1200px; height: 675px;
    display: flex; align-items: center; justify-content: center; gap: 30px;
  }
  .card {
    position: relative; width: 540px; height: 309px; overflow: hidden;
    box-shadow: 0 10px 30px rgba(0,0,0,.45);
  }

  /* Brand lockup */
  .brand { position: absolute; }
  .wordmark {
    display: flex; align-items: center; gap: 10px;
    font-weight: 500; color: var(--navy); letter-spacing: .02em; line-height: 1.15;
  }
  .wordmark-dot {
    width: 16px; height: 16px; border-radius: 50%; background: var(--brand-blue); flex: none;
  }
  .tagline {
    margin-top: 8px; font-size: 9.5px; font-weight: 500; color: var(--grey); letter-spacing: .02em;
  }

  /* Front */
  .card-front { background: var(--white); }
  .card-front .brand { left: 34px; top: 112px; width: 250px; }
  .card-front .wordmark { font-size: 21px; }
  .card-front .tagline { padding-left: 26px; }

  .contact { position: absolute; left: 300px; top: 70px; width: 226px; color: var(--ink); }
  .contact-name { font-size: 15px; font-weight: 700; color: var(--brand-blue); line-height: 1.1; }
  .contact-title { font-size: 13px; font-weight: 500; margin-bottom: 9px; }
  .contact-list { list-style: none; font-size: 10px; color: var(--grey); }
  .contact-list li { display: flex; align-items: center; gap: 7px; line-height: 1.6; white-space: nowrap; }
  .contact-list svg { width: 9px; height: 9px; fill: var(--brand-blue); flex: none; }
  .contact-web { margin-top: 4px; font-size: 10.5px; font-weight: 700; color: var(--ink); white-space: nowrap; }
  .contact-web span { color: var(--brand-blue); }
  .front-band { position: absolute; left: 0; bottom: 0; width: 540px; height: 30px; }

  /* Back */
  .card-back {
    background: radial-gradient(circle at 30% 40%, #1f3380 0%, var(--navy) 45%, var(--navy-deep) 100%);
  }
  .card-back .brand { left: 0; right: 0; top: 126px; text-align: center; }
  .card-back .wordmark { justify-content: center; font-size: 26px; color: var(--white); }
  .card-back .wordmark-dot { width: 20px; height: 20px; background: var(--sky); }
  .card-back .tagline { font-size: 11px; color: #b9c6ea; }
</style>
</head>
<body>
<main class="canvas">
  <section class="card card-front" aria-label="Business card front">
    <div class="brand">
      <div class="wordmark"><span class="wordmark-dot"></span><span>TelmaNord<br>Partners.com.au</span></div>
      <p class="tagline">Steady Ledger Answers... that deliver.</p>
    </div>

    <div class="contact">
      <p class="contact-name">Doug Hallett</p>
      <p class="contact-title">Principal</p>
      <ul class="contact-list">
        <li>
          <svg viewBox="0 0 10 10" aria-hidden="true"><path d="M2 0h2l1 3-1.5 1a6 6 0 0 0 2.5 2.5L7 5l3 1v2a2 2 0 0 1-2 2A8 8 0 0 1 0 2a2 2 0 0 1 2-2z"/></svg>
          1800 493 518
        </li>
        <li>
          <svg viewBox="0 0 10 10" aria-hidden="true"><path d="M2.5 0h5a1 1 0 0 1 1 1v8a1 1 0 0 1-1 1h-5a1 1 0 0 1-1-1V1a1 1 0 0 1 1-1zm.5 1.5v6h4v-6z"/></svg>
          0412 658 071
        </li>
        <li>
          <svg viewBox="0 0 10 10" aria-hidden="true"><path d="M0 2h10v6H0zm1 1 4 3 4-3v-.2H1z"/></svg>
          admin@telmanordpartners.com.au
        </li>
      </ul>
      <p class="contact-web">www.<span>telmanordpartners.com.au</span></p>
    </div>

    <svg class="front-band" viewBox="0 0 540 30" preserveAspectRatio="none" aria-hidden="true">
      <rect x="0" y="18" width="540" height="12" fill="var(--navy)"/>
      <polygon points="300,18 540,4 540,30 300,30" fill="var(--brand-blue)"/>
    </svg>
  </section>

  <section class="card card-back" aria-label="Business card back">
    <div class="brand">
      <div class="wordmark"><span class="wordmark-dot"></span>TelmaNord Partners.com.au</div>
      <p class="tagline">Steady Ledger Answers... that deliver.</p>
    </div>
  </section>
</main>
</body>
</html>
```